Business card design

I need my logo on this card, things I need the card to have on it
licensed and insured.
owner operators Milo & Trent Halvorsen
my phone number 5083716254
Disaster Recovery, Storm Damage Restoration, Proactive Disaster Plan Management, Roof Repair/Restoration Structural Repair and Reconstruction, Emergency Boarding and Tarping Service, Perimeter Fencing, Emergency Tree Removal,

```html
<!DOCTYPE html>
<html lang="en">
<head>
<meta charset="utf-8">
<title>Halvorsen's Construction — Business Card</title>
<link rel="stylesheet" href="https://fonts.googleapis.com/css2?family=Nunito:wght@400;600&display=swap">
<style>
  :root {
    --backdrop: #9b9b9b;
    --brand-blue: #3d92d0;
    --brand-gray: #707074;
    --card-white: #ffffff;
    --ink: #1d1d1f;
  }
  * { margin: 0; padding: 0; box-sizing: border-box; }
  html, body { width: 1093px; height: 1200px; overflow: hidden; }
  body {
    background: var(--backdrop);
    font-family: "Nunito", sans-serif;
    position: relative;
  }
  .card {
    position: absolute;
    border-radius: 24px;
    overflow: hidden;
  }
  .card--front {
    left: 265px; top: 224px; width: 580px; height: 362px;
    background: var(--brand-blue);
    color: var(--card-white);
  }
  .card--back {
    left: 261px; top: 619px; width: 596px; height: 363px;
    background: var(--card-white);
    color: var(--ink);
  }
  .company-name {
    position: absolute;
    text-align: center;
    font-weight: 400;
    line-height: 1;
  }
  .company-name__main { display: block; font-size: 29px; letter-spacing: 0.5px; }
  .company-name__sub { display: block; font-size: 10px; letter-spacing: 6.5px; margin-top: 8px; }
  .card--front .company-name { left: 40px; width: 220px; top: 160px; color: var(--card-white); }
  .card--back .company-name { left: 45px; width: 224px; top: 175px; color: var(--brand-blue); }
  .divider {
    position: absolute;
    width: 1px;
  }
  .card--front .divider { left: 268px; top: 85px; height: 186px; background: rgba(255,255,255,0.85); }
  .card--back .divider { left: 293px; top: 83px; height: 176px; background: var(--brand-gray); }
  .services {
    position: absolute;
    left: 282px; top: 88px; width: 290px;
    list-style: none;
    font-size: 14px;
    line-height: 16px;
  }
  .services li {
    position: relative;
    padding-left: 13px;
    margin-bottom: 9.3px;
  }
  .services li::before {
    content: "";
    position: absolute;
    left: 0; top: 5px;
    width: 7px; height: 7px;
    border-radius: 50%;
    background: var(--card-white);
  }
  .contact {
    position: absolute;
    left: 304px; top: 84px; width: 290px;
  }
  .contact__names {
    font-size: 22px; font-weight: 400;
    color: var(--brand-blue);
    line-height: 1.1;
    white-space: nowrap;
  }
  .contact__role { font-size: 13px; margin-top: 3px; }
  .contact__address { font-size: 14px; line-height: 17px; margin-top: 18px; }
  .contact__lines { list-style: none; margin-top: 15px; font-size: 13.5px; }
  .contact__lines li { display: flex; align-items: center; height: 23.5px; }
  .contact__icon { width: 15px; height: 15px; margin-right: 9px; flex: none; }
  .card__wave { position: absolute; left: 0; top: 0; width: 596px; height: 363px; }
</style>
</head>
<body>

<section class="card card--front" aria-label="Card front">
  <div class="company-name">
    <span class="company-name__main">HALVORSEN'S</span>
    <span class="company-name__sub">CONSTRUCTION L.L.C</span>
  </div>
  <div class="divider"></div>
  <ul class="services">
    <li>Disaster Recovery</li>
    <li>Storm Damage Restoration</li>
    <li>Proactive Disaster Plan Management</li>
    <li>Perimeter Fencing</li>
    <li>Emergency Boarding and Tarping Service</li>
    <li>Emergency Tree Removal</li>
    <li>Roof Repair/Restoration Structural Repair And Reconstruction</li>
  </ul>
</section>

<section class="card card--back" aria-label="Card back">
  <svg class="card__wave" viewBox="0 0 596 363" aria-hidden="true">
    <path d="M0 306 C70 335 180 330 300 312 C380 300 430 290 430 286 C380 290 300 304 220 316 C130 330 50 330 0 318 Z" fill="#707074"/>
    <path d="M0 343 C120 372 250 340 360 310 C440 290 530 275 596 293 L596 363 L0 363 Z" fill="#3d92d0"/>
    <path d="M0 330 C120 355 260 325 380 305 C430 297 470 296 490 297" fill="none" stroke="#ffffff" stroke-width="1.2"/>
  </svg>

  <div class="company-name">
    <span class="company-name__main">HALVORSEN'S</span>
    <span class="company-name__sub">CONSTRUCTION L.L.C</span>
  </div>
  <div class="divider"></div>

  <div class="contact">
    <p class="contact__names">Milo &amp; Trent Halvorsen</p>
    <p class="contact__role">owner operators</p>
    <p class="contact__address">48 Cedar Hollow Road<br>Brandon, MS 39042</p>
    <ul class="contact__lines">
      <li>
        <svg class="contact__icon" viewBox="0 0 16 16" aria-label="Phone">
          <path d="M1 6 C1 3 15 3 15 6 L15 7 L11 7 L11 5.5 L5 5.5 L5 7 L1 7 Z" fill="#3d92d0"/>
          <path d="M4 8 L12 8 L14 14 L2 14 Z" fill="#3d92d0"/>
          <circle cx="8" cy="11" r="1.8" fill="#fff"/>
        </svg>
        <span>&nbsp;5083716254</span>
      </li>
      <li>
        <svg class="contact__icon" viewBox="0 0 16 16" aria-label="Email">
          <rect x="1" y="3" width="14" height="10" rx="1" fill="#3d92d0"/>
          <path d="M1.5 3.8 L8 9 L14.5 3.8" fill="none" stroke="#fff" stroke-width="1.2"/>
        </svg>
        <span>info@halvorsenbuild.com</span>
      </li>
      <li>
        <svg class="contact__icon" viewBox="0 0 16 16" aria-label="Website">
          <circle cx="8" cy="8" r="7" fill="#3d92d0"/>
          <path d="M4 4 C6 5 5 7 7 7 C8 8 6 10 7 12 M10 3 C11 5 12 5 13 6 M10 10 C11 9 12 10 12 12" fill="none" stroke="#fff" stroke-width="1.2"/>
        </svg>
        <span>www.halvorsenbuild.com</span>
      </li>
    </ul>
  </div>
</section>

</body>
</html>
```